Logo, Web and Mobile Designs for enterprise social media platform

All the details are in the attached document, please start reading the scope document first which explains what is this project about and the details about the needed deliverables, after that please read the UI_Requirements document which will detail what is expected regarding the coded web version since this is a coded contest, it is very important that you meet the UI requirements or suggest something else but we will need to agree first before working on the coded version

Good Luck

Target Market(s)

Enterprise Social Media

Industry/Entity Type

Media

Coding

Coded - Design and coding required

Number of Pages Required

5+ page

Font styles to use
Sans Serif

Requirements
Must have
• All the must haves are listed in the scope document so please check before you start

```html
<!DOCTYPE html>
<html lang="en">
<head>
<meta charset="utf-8">
<title>Teamora – Business Opportunity Network</title>
<link href="https://fonts.googleapis.com/css2?family=Roboto:wght@400;500&family=Open+Sans:ital,wght@0,400;1,400&display=swap" rel="stylesheet">
<style>
:root{
  --page:#ececec;
  --panel:#ffffff;
  --panel-head:#f7f8f9;
  --line:#e3e5e7;
  --field-line:#dcdfe2;
  --text:#4a4f55;
  --muted:#6a6f75;
  --blue:#2a9fd6;
  --blue-dark:#1f8cc0;
  --orange:#f29a0a;
  --orange-acc:#f07c1b;
  --footer:#2a8dbf;
  --photo-a:#8a7a6c;
  --photo-b:#cfd6dc;
}
*{box-sizing:border-box;margin:0;padding:0}
html,body{width:671px;height:1200px;overflow:hidden}
body{position:relative;background:var(--page);font-family:"Roboto",Arial,sans-serif;color:var(--text)}
.abs{position:absolute}

/* top bar */
.topbar{position:absolute;left:0;top:0;width:671px;height:38px;background:linear-gradient(#fdfdfd,#f3f3f3);border-bottom:1px solid #dedede}
.topbar .sep{position:absolute;top:0;width:1px;height:38px;background:#e4e4e4}
.menu-icon{left:56px;top:14px}
.brand{left:94px;top:9px;display:flex;align-items:center;gap:5px;font-size:17px;font-weight:500;color:var(--blue)}
.brand .mark{width:18px;height:18px;border-radius:50%;background:var(--orange)}
.user{left:417px;top:10px;display:flex;align-items:center;gap:7px;font-size:10px;color:var(--text)}
.user .avatar{width:18px;height:18px;border-radius:50%;background:linear-gradient(135deg,#555,#999)}
.badge{position:absolute;width:11px;height:9px;border-radius:5px;font-size:6px;line-height:9px;text-align:center;color:#fff}

/* panels */
.panel{position:absolute;left:55px;width:560px;background:var(--panel);border:1px solid #e0e2e4}
.panel-head{height:27px;background:var(--panel-head);border-bottom:1px solid var(--line);padding:0 11px;font-size:8.5px;line-height:27px;letter-spacing:.1px;color:#3e454c;position:relative}
.label{position:absolute;font-size:8px;color:var(--muted)}
.field{position:absolute;border:1px solid var(--field-line);background:#fff;border-radius:2px}
.btn{position:absolute;border-radius:2px;color:#fff;font-size:8px;text-align:center;display:flex;align-items:center;justify-content:center;gap:4px;letter-spacing:.2px}
.btn-orange{background:var(--orange);font-size:8.5px}
.btn-blue{background:var(--blue);font-size:7px}
.divider{position:absolute;left:0;width:558px;height:1px;background:#eef0f1}

.group-photo{position:absolute;border-radius:50%;background:linear-gradient(135deg,var(--photo-a),var(--photo-b))}
.group-title{position:absolute;font-size:9px;color:var(--blue)}
.group-desc{position:absolute;font-family:"Open Sans",Arial,sans-serif;font-style:italic;font-size:6px;line-height:10px;color:#555}
.member-title{position:absolute;font-size:8.5px;color:#333}
.chev{position:absolute}

.radio{position:absolute;display:flex;align-items:center;gap:6px;font-size:7px;color:var(--muted)}
.radio i{width:8px;height:8px;border-radius:50%;border:1px solid #ccc;display:block;position:relative}
.radio i.on::after{content:"";position:absolute;left:2px;top:2px;width:2px;height:2px;border-radius:50%;background:#999}

.acc{position:absolute;left:104px;width:264px}
.acc-head{height:20px;border:1px solid #e6e8ea;background:#f8f9fa;font-size:6.5px;line-height:18px;padding-left:8px;position:relative;color:#444}
.acc-toggle{position:absolute;right:0;top:-1px;width:19px;height:20px;display:flex;align-items:center;justify-content:center;color:var(--orange-acc);font-size:11px}
.acc-toggle.open{background:var(--orange-acc);color:#fff}
.acc-body{border:1px solid #e6e8ea;border-top:none;height:58px;padding:9px 13px;font-family:"Open Sans",Arial,sans-serif;font-size:5.6px;line-height:11.5px;color:#444}

/* footer */
.footer{position:absolute;left:0;top:1117px;width:671px;height:83px;background:var(--footer);color:#fff;text-align:center}
.social{position:absolute;left:287px;top:15px;display:flex;gap:8px}
.social span{width:13px;height:13px;background:#fff;border-radius:2px;display:block}
.footer-links{position:absolute;left:0;width:671px;top:39px;font-size:8px;letter-spacing:.1px}
.copyright{position:absolute;left:0;width:671px;top:56px;font-size:7.5px}
</style>
</head>
<body>

<header class="topbar">
  <svg class="abs menu-icon" width="11" height="9" viewBox="0 0 11 9"><rect y="0" width="11" height="1.6" fill="#777"/><rect y="3.7" width="11" height="1.6" fill="#777"/><rect y="7.4" width="11" height="1.6" fill="#777"/></svg>
  <span class="sep" style="left:80px"></span>
  <div class="abs brand"><span class="mark"></span>Teamora</div>
  <div class="abs user"><span class="avatar"></span>Dana Reyes
    <svg width="8" height="5" viewBox="0 0 8 5"><path d="M0 0h8L4 5z" fill="#555"/></svg></div>
  <span class="sep" style="left:516px"></span>
  <svg class="abs" style="left:529px;top:14px" width="11" height="11" viewBox="0 0 11 11"><rect width="8" height="2" fill="#777"/><rect y="4" width="10" height="2" fill="#777"/><rect y="8" width="6" height="2" fill="#777"/></svg>
  <span class="badge" style="left:536px;top:9px;background:var(--orange)">8</span>
  <span class="sep" style="left:552px"></span>
  <svg class="abs" style="left:565px;top:14px" width="11" height="11" viewBox="0 0 11 11"><circle cx="4.5" cy="4.5" r="3.5" fill="none" stroke="#666" stroke-width="1.6"/><path d="M7 7l3.3 3.3" stroke="#666" stroke-width="1.8"/></svg>
  <span class="sep" style="left:588px"></span>
  <svg class="abs" style="left:600px;top:14px" width="10" height="11" viewBox="0 0 10 11"><path d="M5 0c2.5 0 3.5 2 3.5 4v3l1.5 1.5H0L1.5 7V4C1.5 2 2.5 0 5 0z" fill="#666"/><circle cx="5" cy="10" r="1.2" fill="#666"/></svg>
  <span class="badge" style="left:603px;top:9px;background:var(--blue)">8</span>
</header>

<section class="panel" style="top:62px;height:218px">
  <div class="panel-head">BUSINESS OPPORTUNITY NETWORK
    <svg class="abs" style="right:15px;top:11px" width="4" height="6" viewBox="0 0 4 6"><path d="M0 0l4 3-4 3" fill="none" stroke="#aaa"/></svg></div>
  <span class="label" style="left:21px;top:50px">Name : *</span>
  <span class="field" style="left:103px;top:44px;width:262px;height:21px"></span>
  <span class="label" style="left:21px;top:79px">About : *</span>
  <span class="field" style="left:103px;top:73px;width:262px;height:21px"></span>
  <span class="label" style="left:21px;top:109px">Description : *</span>
  <span class="field" style="left:103px;top:104px;width:262px;height:70px"></span>
  <span class="btn btn-orange" style="left:103px;top:184px;width:63px;height:18px">UPDATE</span>
</section>

<section class="panel" style="top:293px;height:397px">
  <div class="panel-head">GROUPS NAME</div>
  <span class="btn btn-blue" style="left:491px;top:5px;width:62px;height:18px">ADD MORE <b>+</b></span>
  <span class="field" style="left:13px;top:38px;width:214px;height:19px;font-size:5.5px;line-height:17px;padding-left:8px;color:#777">add a new group name</span>
  <span class="btn btn-blue" style="left:234px;top:38px;width:80px;height:19px"><b>+</b> ADD NEW GROUP</span>
  <span class="divider" style="top:70px"></span>

  <span class="group-photo" role="img" aria-label="Administrators group photo" style="left:16px;top:80px;width:38px;height:38px"></span>
  <span class="group-title" style="left:64px;top:80px">Administrators</span>
  <span class="group-desc" style="left:64px;top:93px">Lorem ipsum dolor sit amet,<br>consectetur adipiscing elit, sed do</span>
  <svg class="chev" style="left:544px;top:94px" width="7" height="7" viewBox="0 0 7 7"><path d="M0 0l3.5 3 3.5-3M0 3.5l3.5 3 3.5-3" fill="none" stroke="#555"/></svg>
  <span class="divider" style="top:128px"></span>

  <span class="group-photo" role="img" aria-label="Member photo" style="left:23px;top:141px;width:32px;height:32px"></span>
  <span class="member-title" style="left:64px;top:145px">Nemo enim ipsam voluptatem</span>
  <span class="group-desc" style="left:64px;top:158px">Lorem ipsum dolor sit amet, consectetur adipiscing elit, sed do</span>
  <span class="group-photo" role="img" aria-label="Member photo" style="left:23px;top:184px;width:32px;height:32px;background:linear-gradient(135deg,#e6eaee,#9fb0bf)"></span>
  <span class="member-title" style="left:64px;top:188px">Nemo enim ipsam voluptatem</span>
  <span class="group-desc" style="left:64px;top:201px">Lorem ipsum dolor sit amet, consectetur adipiscing elit, sed do</span>
  <span class="group-photo" role="img" aria-label="Member photo" style="left:23px;top:228px;width:32px;height:32px;background:linear-gradient(135deg,#eef0f2,#a9b2bb)"></span>
  <span class="member-title" style="left:64px;top:232px">Nemo enim ipsam voluptatem</span>
  <span class="group-desc" style="left:64px;top:245px">Lorem ipsum dolor sit amet, consectetur adipiscing elit, sed do</span>
  <span class="divider" style="top:277px"></span>

  <span class="group-photo" role="img" aria-label="Buyers group photo" style="left:16px;top:286px;width:38px;height:38px;background:linear-gradient(135deg,#7ea7c9,#d9d2c8)"></span>
  <span class="group-title" style="left:64px;top:286px">Buyers</span>
  <span class="group-desc" style="left:64px;top:299px">Lorem ipsum dolor sit amet,<br>consectetur adipiscing elit, sed do</span>
  <svg class="chev" style="left:544px;top:301px" width="7" height="7" viewBox="0 0 7 7"><path d="M0 3.5l3.5-3 3.5 3M0 7l3.5-3 3.5 3" fill="none" stroke="#555"/></svg>
  <span class="divider" style="top:334px"></span>

  <span class="group-photo" role="img" aria-label="Sellers group photo" style="left:16px;top:344px;width:38px;height:38px;background:linear-gradient(135deg,#d8d4cc,#5e6670)"></span>
  <span class="group-title" style="left:64px;top:344px">Sellers</span>
  <span class="group-desc" style="left:64px;top:357px">Lorem ipsum dolor sit amet,<br>consectetur adipiscing elit, sed do</span>
  <svg class="chev" style="left:544px;top:359px" width="7" height="7" viewBox="0 0 7 7"><path d="M0 3.5l3.5-3 3.5 3M0 7l3.5-3 3.5 3" fill="none" stroke="#555"/></svg>
</section>

<section class="panel" style="top:704px;height:386px">
  <div class="panel-head">BUSINESS OPPORTUNITY ITEMS</div>
  <span class="label" style="left:23px;top:54px">Name : *</span>
  <span class="field" style="left:106px;top:48px;width:262px;height:21px"></span>
  <span class="label" style="left:23px;top:83px">Description : *</span>
  <span class="field" style="left:106px;top:77px;width:262px;height:69px"></span>
  <span class="field" style="left:106px;top:154px;width:188px;height:21px"></span>
  <span class="btn btn-blue" style="left:293px;top:154px;width:75px;height:21px;font-size:8px">UPLOADED</span>
  <span class="radio" style="left:106px;top:192px"><i></i>Public</span>
  <span class="radio" style="left:157px;top:192px"><i class="on"></i>Private</span>
  <span class="btn btn-orange" style="left:105px;top:206px;width:64px;height:18px">ADD</span>

  <div class="acc" style="top:242px">
    <div class="acc-head">Cedar Ridge 6th of October<span class="acc-toggle open">−</span></div>
    <div class="acc-body">Lorem ipsum dolor sit amet, consectetur adipiscing elit, sed do eiusmod tempor incididunt ut labore et dolore magna aliqua. Ut enim ad minim veniam, quis nostrud exercitation ullamco laboris nisi ut aliquip</div>
  </div>
  <div class="acc" style="top:323px"><div class="acc-head">Cedar Ridge New Cairo<span class="acc-toggle">+</span></div></div>
  <div class="acc" style="top:347px"><div class="acc-head">Cedar Ridge North Coast<span class="acc-toggle">+</span></div></div>
</section>

<footer class="footer">
  <div class="social"><span></span><span></span><span></span><span></span><span></span></div>
  <div class="footer-links">Home &nbsp;/&nbsp; Contact &nbsp;/&nbsp; Topics &nbsp;/&nbsp; Posts and Comments &nbsp;/&nbsp; Discussion &nbsp;/&nbsp; Videos Links</div>
  <div class="copyright">Copyright @ 2015 - 2015.Teamora. All Rights Reserved.</div>
</footer>

</body>
</html>
```